New Business Card Design Project

We require a business card design for Vexalund, a newly established Indian company.
Our focus is on the development, manufacturing, and export of a diverse array of pharmaceutical products on a global scale. The card should convey a professional appearance, as our primary markets are in Africa, China, and Southeast Asian nations.
We envision a two-sided business card, with the reverse side dedicated to a logo set against a solid color or an elegantly designed pattern. The corners should be rounded. We would appreciate seeing both horizontal and vertical design options. We trust the designer to utilize their expertise in creating this design.

The content for the business card is included in the attached Word file.

Target Market(s)

Our primary markets are in Africa, China, and Southeast Asian, Latin America, Maldives, Sri Lanka

Industry/Entity Type

Pharmaceutical Manufacturing and Export

Contact Information for Business Card

Colors

Designer to choose colors to be used in the design.

Requirements
Must have
• The reverse side of the business card features solely the logo along with the tagline, "Care for Every Day."
Should not have
• The logo should not exceed two instances, encompassing both the front and back sides of the card.

```html
<!DOCTYPE html>
<html lang="en">
<head>
<meta charset="utf-8">
<title>Vexalund Business Card</title>
<link href="https://fonts.googleapis.com/css2?family=Montserrat:wght@700&family=Arimo:wght@400&display=swap" rel="stylesheet">
<style>
  :root {
    --backdrop: #3f3f3f;
    --brand-blue: #29a9e1;
    --accent-red: #ef5f4c;
    --paper: #ffffff;
  }
  * { box-sizing: border-box; margin: 0; padding: 0; }
  html, body { width: 1200px; height: 803px; overflow: hidden; }
  body {
    background: var(--backdrop);
    display: flex;
    align-items: center;
    justify-content: center;
    gap: 50px;
    font-family: "Arimo", Arial, sans-serif;
  }
  .card {
    width: 530px;
    height: 303px;
    border-radius: 22px;
    overflow: hidden;
    position: relative;
    box-shadow: 0 12px 30px rgba(0,0,0,0.35);
  }
  /* Front */
  .card-front { background: var(--paper); display: flex; flex-direction: column; }
  .front-top {
    height: 150px;
    display: flex;
    align-items: center;
    justify-content: center;
  }
  .accent-rule { height: 5px; background: var(--accent-red); }
  .front-bottom {
    flex: 1;
    background: var(--brand-blue);
    color: var(--paper);
    display: flex;
    align-items: center;
    padding: 0 34px;
    gap: 26px;
  }
  .wordmark {
    font-family: "Montserrat", sans-serif;
    font-weight: 700;
    display: flex;
    align-items: center;
    gap: 12px;
    white-space: nowrap;
  }
  .wordmark-dot { border-radius: 50%; flex: none; }
  .front-top .wordmark { font-size: 44px; color: var(--brand-blue); }
  .front-top .wordmark-dot { width: 26px; height: 26px; background: var(--accent-red); }
  .person { text-align: right; white-space: nowrap; }
  .person-name {
    font-family: "Montserrat", sans-serif;
    font-weight: 700;
    font-size: 22px;
    letter-spacing: 0.3px;
  }
  .person-role { font-size: 12px; margin-top: 2px; }
  .person-email { font-size: 13px; margin-top: 4px; }
  .divider { width: 1px; align-self: stretch; margin: 28px 0; background: rgba(255,255,255,0.8); }
  .contact { font-size: 13px; line-height: 1.45; white-space: nowrap; }
  .contact-address { margin-bottom: 8px; }
  .contact-line { display: flex; align-items: center; gap: 8px; }
  .contact-line svg { width: 12px; height: 12px; flex: none; }
  /* Back */
  .card-back {
    background: var(--brand-blue);
    color: var(--paper);
    display: flex;
    flex-direction: column;
    align-items: center;
    justify-content: center;
  }
  .card-back .wordmark { font-size: 54px; }
  .card-back .wordmark-dot { width: 30px; height: 30px; background: var(--accent-red); }
  .tagline { margin-top: 22px; font-size: 15px; letter-spacing: 0.4px; }
</style>
</head>
<body>
  <section class="card card-front" aria-label="Business card front">
    <div class="front-top">
      <div class="wordmark"><span class="wordmark-dot"></span>Vexalund</div>
    </div>
    <div class="accent-rule"></div>
    <div class="front-bottom">
      <div class="person">
        <div class="person-name">Rohan K. Malvade</div>
        <div class="person-role">CEO</div>
        <div class="person-email">rmalvade@vexalund.com</div>
      </div>
      <div class="divider"></div>
      <div class="contact">
        <div class="contact-address">14, Nilgiri Colony, Nashik<br>422002, India</div>
        <div class="contact-line">
          <svg viewBox="0 0 24 24" aria-hidden="true"><path fill="#fff" d="M6.6 10.8a15.1 15.1 0 0 0 6.6 6.6l2.2-2.2a1 1 0 0 1 1-.25 11.4 11.4 0 0 0 3.6.57 1 1 0 0 1 1 1V20a1 1 0 0 1-1 1A17 17 0 0 1 3 4a1 1 0 0 1 1-1h3.5a1 1 0 0 1 1 1c0 1.25.2 2.45.57 3.57a1 1 0 0 1-.25 1z"/></svg>
          +919800012345
        </div>
        <div class="contact-line">
          <svg viewBox="0 0 24 24" aria-hidden="true"><circle cx="12" cy="12" r="9" fill="none" stroke="#fff" stroke-width="2.4"/><path d="M3 12h18M12 3c3 3.2 3 14.8 0 18M12 3c-3 3.2-3 14.8 0 18" fill="none" stroke="#fff" stroke-width="1.8"/></svg>
          www.vexalund.com
        </div>
      </div>
    </div>
  </section>

  <section class="card card-back" aria-label="Business card back">
    <div class="wordmark"><span class="wordmark-dot"></span>Vexalund</div>
    <div class="tagline">Care for Every Day</div>
  </section>
</body>
</html>
```